Contemporary new French wine brand needs logo and series of label design

to design a new contemporary logo and series of labels for a new French wine brand. We hope to attract not just current French wine drinkers but new ones who may appreciate a less traditional and more modern style.
Updates

Reason: we are wanting to extend the project for a few days more to receive more submissions since we had fewer designs submitted than we were expecting, maybe because of the holidays.

Target Market(s)

people who follow the arts community (eg. music, theatre, visual/video arts, dance) --- all mature ages.

Industry/Entity Type

French Wine

Requirements
Must have
• a clear, memorable treatment for the name MORIVAL with accompanying logo.
Nice to have
• embossing, matte/gloss refinement, tasteful foil stamping, coated stock for the whites to help the integrity of the paper in and out of ice buckets. A combo of say, three types of fonts; a semi custom font for the brand name Morival and maybe a script and one other.
Should not have
• not traditional French

```html
<!DOCTYPE html>
<html lang="en">
<head>
<meta charset="utf-8">
<title>Morival – Cabernet Franc label</title>
<link rel="stylesheet" href="https://fonts.googleapis.com/css2?family=PT+Sans&family=Caveat&family=Tinos&display=swap">
<style>
  :root {
    --page: #ecece6;
    --glass: #34501a;
    --glass-deep: #263d10;
    --band-top: #e6dcf3;
    --band-bottom: #d9cdea;
    --frame: #d8d0e4;
    --ink-light: #f4f0fa;
    --ink-dark: #2a2530;
  }
  html, body {
    margin: 0;
    width: 900px;
    height: 1200px;
    overflow: hidden;
    background: var(--page);
  }
  .label {
    position: absolute;
    left: 78px;
    top: 243px;
    width: 744px;
    height: 714px;
    background: linear-gradient(180deg, var(--glass) 0%, var(--glass-deep) 100%);
  }
  .label__band {
    position: absolute;
    left: 0;
    right: 0;
    top: 339px;
    bottom: 0;
    background: linear-gradient(180deg, var(--band-top), var(--band-bottom));
  }
  .label__frame {
    position: absolute;
    left: 21px;
    top: 6px;
    width: 717px;
    height: 672px;
    border: 3px solid var(--frame);
    box-sizing: border-box;
  }
  .label__mark {
    position: absolute;
    left: 354px;
    top: 126px;
    width: 36px;
    height: 36px;
    background: var(--ink-light);
  }
  .label__brand {
    position: absolute;
    left: 0;
    right: 0;
    top: 262px;
    text-align: center;
    font-family: "PT Sans", sans-serif;
    font-size: 84px;
    line-height: 1;
    color: var(--ink-light);
    letter-spacing: -1px;
  }
  .label__variety {
    position: absolute;
    left: 0;
    right: 0;
    top: 500px;
    text-align: center;
    font-family: "Caveat", cursive;
    font-size: 40px;
    letter-spacing: 8px;
    color: var(--ink-dark);
  }
  .label__region {
    position: absolute;
    left: 0;
    right: 0;
    top: 620px;
    text-align: center;
    font-family: "Tinos", serif;
    font-size: 22px;
    color: var(--ink-dark);
  }
</style>
</head>
<body>
  <main class="label">
    <div class="label__band"></div>
    <div class="label__frame"></div>
    <div class="label__mark"></div>
    <h1 class="label__brand" style="margin:0;font-weight:400;">Morival</h1>
    <p class="label__variety" style="margin:0;">Cabernet Franc</p>
    <p class="label__region" style="margin:0;">burgundy</p>
  </main>
</body>
</html>
```